Allied Health team of Physiotherapists & Occupational Therapists seek a business card design

We have our new logo, we now need our new business cards and stationary. Tidewell: Oedema & Family Clinic is seeking a generic card design to represent our whole team and individual cards for each therapist that incorporates our new logo to communicate our holistic approach that is calming, nuturing, supportive and welcoming.
Our Physiotherapists and Occupational Therapists assess, treat and provide education for people who are at risk of or who have lymphoedema. This is often as a result of treatment for cancer. We provide pre-operative and post-operative management and cancer rehabilitation in our Pilates studio. Our team also consists of Physiotherapists who have a strong interest in pelvic floor and continence management for both men and women.

Target Market(s)

Mainly women health conscious

Industry/Entity Type

Allied Health: Physiotherapy / Occupational Therapy

Contact Information for Business Card

Address: 14 Gallivant Ave Frankston 3199 Phone: 84316570 fax: 8431 6578 Email: info@tidewellcareservices.com.au Website: tidewellcareservices.com.au Facebook address: facebook.com/TidewellOedemaAndFamilyCareClinic. Room to write appointments. Individual cards need to have name, office email and individual email and professional details

Requirements
Must have
• Logo as per uploaded documents

```html
<!DOCTYPE html>
<html lang="en">
<head>
<meta charset="utf-8">
<title>Tidewell: Oedema &amp; Family Clinic – Business Cards</title>
<link rel="stylesheet" href="https://fonts.googleapis.com/css2?family=Cinzel:wght@500;600&family=Open+Sans:wght@400;600&display=swap">
<style>
  :root {
    --backdrop: #e7e4e2;
    --card-white: #ffffff;
    --peach: #f8ae83;
    --peach-deep: #f0a070;
    --sage: #c6ccc4;
    --ink: #2b2b2b;
    --on-peach: #ffffff;
    --shadow: rgba(60, 50, 45, 0.18);
  }
  * { box-sizing: border-box; margin: 0; padding: 0; }
  html, body { width: 1200px; height: 997px; overflow: hidden; }
  body {
    background: var(--backdrop);
    font-family: "Open Sans", sans-serif;
    position: relative;
  }
  .card {
    position: absolute;
    width: 540px;
    height: 309px;
    border-radius: 3px;
    overflow: hidden;
    box-shadow: 0 6px 18px var(--shadow);
  }
  .card-front { left: 70px; top: 170px; background: var(--card-white); }
  .card-back { left: 600px; top: 500px; background: var(--peach); }

  .card-art { position: absolute; inset: 0; width: 100%; height: 100%; }

  .holder { position: absolute; left: 40px; top: 92px; }
  .holder-name {
    font-family: "Cinzel", serif;
    font-weight: 600;
    font-size: 22px;
    color: var(--peach-deep);
    letter-spacing: 0.5px;
    line-height: 1;
  }
  .holder-title { font-size: 11.5px; color: var(--ink); margin-top: 3px; }

  .brand-front {
    position: absolute; right: 38px; top: 34px;
    display: flex; flex-direction: column; align-items: center; gap: 6px;
    font-family: "Cinzel", serif; font-weight: 600; color: var(--peach-deep);
    text-align: center;
  }
  .brand-front .brand-dot {
    width: 14px; height: 14px; border-radius: 50%; background: var(--peach-deep);
  }
  .brand-front .brand-name { font-size: 22px; line-height: 1; }
  .brand-front .brand-sub { font-size: 9px; letter-spacing: 1px; }

  .address {
    position: absolute; right: 28px; top: 150px;
    font-size: 9.5px; line-height: 1.45; color: var(--on-peach); text-align: right;
  }

  .contacts {
    position: absolute; left: 40px; top: 206px;
    list-style: none; color: var(--on-peach); font-size: 11px;
  }
  .contacts li { display: flex; align-items: center; gap: 9px; height: 20px; }
  .contacts svg { width: 12px; height: 12px; fill: var(--on-peach); flex: none; }

  .brand-back {
    position: absolute; inset: 0;
    display: flex; align-items: center; justify-content: center;
  }
  .brand-back-mark {
    width: 168px; height: 168px; border-radius: 50%;
    border: 2px solid var(--on-peach);
    display: flex; flex-direction: column; align-items: center; justify-content: center;
    font-family: "Cinzel", serif; font-weight: 600; color: var(--on-peach);
    text-align: center; gap: 6px;
  }
  .brand-back-mark .brand-name { font-size: 28px; line-height: 1; }
  .brand-back-mark .brand-sub { font-size: 10px; letter-spacing: 1px; line-height: 1.3; }
</style>
</head>
<body>

<section class="card card-front" aria-label="Business card, front">
  <svg class="card-art" viewBox="0 0 540 309" preserveAspectRatio="none" aria-hidden="true">
    <path d="M0 205 C 150 170, 260 150, 340 120 C 420 90, 480 70, 540 60 L540 309 L0 309 Z" fill="var(--sage)"/>
    <path d="M0 218 C 150 185, 265 168, 345 138 C 425 108, 485 92, 540 86 L540 309 L0 309 Z" fill="var(--peach)"/>
    <path d="M250 150 C 360 110, 430 60, 470 18 C 455 60, 400 110, 300 150 Z" fill="var(--sage)"/>
    <path d="M380 125 C 450 100, 500 60, 520 28 C 515 65, 470 100, 400 128 Z" fill="var(--sage)"/>
  </svg>

  <div class="holder">
    <p class="holder-name">MAREN HOLLOWAY</p>
    <p class="holder-title">CEO/Managing Director</p>
  </div>

  <div class="brand-front">
    <span class="brand-dot"></span>
    <span class="brand-name">Tidewell</span>
    <span class="brand-sub">OEDEMA &amp; FAMILY CLINIC</span>
  </div>

  <p class="address">14 Gallivant Ave, Suite 2<br>Frankston 3199</p>

  <ul class="contacts">
    <li><svg viewBox="0 0 24 24"><path d="M6.6 10.8a15 15 0 0 0 6.6 6.6l2.2-2.2c.3-.3.7-.4 1-.2 1.1.4 2.3.6 3.6.6.6 0 1 .4 1 1V20c0 .6-.4 1-1 1A17 17 0 0 1 3 4c0-.6.4-1 1-1h3.5c.6 0 1 .4 1 1 0 1.3.2 2.5.6 3.6.1.3 0 .7-.2 1z"/></svg>8431 6570</li>
    <li><svg viewBox="0 0 24 24"><path d="M7 1h10a2 2 0 0 1 2 2v18a2 2 0 0 1-2 2H7a2 2 0 0 1-2-2V3a2 2 0 0 1 2-2zm0 3v14h10V4zm5 15.5a1 1 0 1 0 0 2 1 1 0 0 0 0-2z"/></svg>8431 6578</li>
    <li><svg viewBox="0 0 24 24"><path d="M2 5h20v14H2zm2 2v.5l8 5 8-5V7zm0 2.8V17h16V9.8l-8 5z"/></svg>info@tidewellcareservices.com.au</li>
    <li><svg viewBox="0 0 24 24"><path d="M12 2a10 10 0 1 0 0 20 10 10 0 0 0 0-20zm6.9 9h-3a15 15 0 0 0-1.3-5.6A8 8 0 0 1 18.9 11zM12 4.1c.9 1.2 1.8 3.6 1.9 6.9h-3.8c.1-3.3 1-5.7 1.9-6.9zM9.4 5.4A15 15 0 0 0 8.1 11h-3a8 8 0 0 1 4.3-5.6zM5.1 13h3a15 15 0 0 0 1.3 5.6A8 8 0 0 1 5.1 13zm6.9 6.9c-.9-1.2-1.8-3.6-1.9-6.9h3.8c-.1 3.3-1 5.7-1.9 6.9zm2.6-1.3a15 15 0 0 0 1.3-5.6h3a8 8 0 0 1-4.3 5.6z"/></svg>tidewellcareservices.com.au</li>
  </ul>
</section>

<section class="card card-back" aria-label="Business card, back">
  <div class="brand-back">
    <div class="brand-back-mark">
      <span class="brand-name">Tidewell</span>
      <span class="brand-sub">OEDEMA &amp;<br>FAMILY CLINIC</span>
    </div>
  </div>
</section>

</body>
</html>
```